Wordpress Design Project for Bankruptcy Law Office in San Francisco

our current website: www.dorvanelilaw-example.com

we would like to re-design it for wordpress to make it faster and a bit more modern.

content should be similar to what we have there right now but also we do family law

please include logo for law office:

Law Office of Marta K. Dolvenidze

Thank you.
Updates

please see attached word document with logos that we like as an example.

we do tend to like color red.  darker red.

Please submit your design variations and logo as soon as possible.   We would like to go over them and make our decision

Reason: Please create couple of more variations of logo for your design, so we can make our decision what we like the most. Please see word doc for samples: Text: Law Office Of Marta K. Dolvenidze

Reason: final touches

Target Market(s)

bankruptcy and family law clients

Industry/Entity Type

Family Law

Requirements
Must have
• see examples of law sites
http://promo.lexorbin-example.com/testimonials

- new logo: Law Office of Marta K. Dolvenidze
- client intake form
- blog
- contact us form

Nice to have
• - map
- red color
- on the front page a nice photo of SF or a happy family

```html
<!DOCTYPE html>
<html lang="en">
<head>
<meta charset="utf-8">
<title>Law Office of Marta K. Dolvenidze</title>
<link rel="stylesheet" href="https://fonts.googleapis.com/css2?family=Cinzel:wght@400;500&family=PT+Sans:wght@400;700&family=PT+Sans+Narrow:wght@400&family=Kalam:wght@700&display=swap">
<style>
:root{
  --bg-deep:#3e030c;
  --bg-mid:#5a0714;
  --red:#a80f1f;
  --red-dark:#760812;
  --red-bright:#b8141f;
  --banner:#b3200f;
  --ink:#111;
  --text:#222;
  --card-title:#3a3a3a;
  --white:#fff;
}
*{margin:0;padding:0;box-sizing:border-box}
html,body{width:1011px;height:1200px;overflow:hidden}
body{background:radial-gradient(ellipse at 50% 30%,var(--bg-mid),var(--bg-deep));font-family:"PT Sans",sans-serif}
.stage{width:1200px;height:1424px;transform:scale(.8425);transform-origin:0 0;position:relative}
.page{position:absolute;left:115px;top:20px;width:970px;height:1377px;background:var(--white);box-shadow:0 0 18px rgba(0,0,0,.5)}
.header{position:absolute;left:0;top:0;width:970px;height:108px;background:linear-gradient(180deg,var(--red-bright),var(--red-dark))}
.brand{position:absolute;left:22px;top:10px;display:flex;align-items:flex-start;gap:12px;color:var(--white);font-family:"Cinzel",serif;font-weight:400}
.brand-square{width:22px;height:22px;background:var(--white);margin-top:6px}
.brand-small{font-size:21px;letter-spacing:1px;text-align:center;padding-left:70px;margin-top:14px}
.brand-name{font-size:30px;letter-spacing:1px;border-top:1px solid rgba(255,255,255,.8);border-bottom:1px solid rgba(255,255,255,.8);line-height:36px;padding-right:4px}
.phone{position:absolute;right:10px;top:58px;display:flex;align-items:center;gap:8px;color:var(--white);font-family:"Cinzel",serif;font-size:27px}
.nav{position:absolute;left:-20px;top:108px;width:1010px;height:44px;background:linear-gradient(180deg,#e6e6e6,#cfcfcf);display:flex;align-items:center;padding-left:42px}
.nav::before,.nav::after{content:"";position:absolute;top:44px;border-top:20px solid #8a8a8a}
.nav::before{left:0;border-left:20px solid transparent}
.nav::after{right:0;border-right:20px solid transparent}
.nav a{font-family:"Cinzel",serif;font-size:17px;text-transform:uppercase;color:var(--ink);text-decoration:none;height:44px;line-height:46px;padding:0 19px;white-space:nowrap}
.nav a.active{background:var(--red);color:var(--white);padding:0 22px}
.hero{position:absolute;left:20px;top:177px;width:933px;height:385px;background:linear-gradient(180deg,#4aa3e4 0%,#bfe3f7 45%,#f2d23a 70%,#6fb42c 100%)}
.hero-tag{position:absolute;right:0;top:66px;width:448px;height:48px;background:var(--banner);color:var(--white);font-family:"Kalam",cursive;font-weight:700;font-size:24px;line-height:50px;text-align:center;white-space:nowrap;overflow:hidden}
.contact{position:absolute;left:18px;top:583px;width:243px;height:337px;background:var(--red);border:3px dotted #b8b8b8;padding:10px 13px}
.contact h2{color:var(--white);font-size:17px;font-weight:700}
.contact p{color:var(--white);font-size:13px;margin:20px 0 14px 8px}
.field{height:25px;margin-bottom:11px;border-radius:3px;background:linear-gradient(180deg,#fff,#cfcfcf);font-size:13px;padding:4px 8px;color:#222}
.field.msg{height:70px}
.submit{position:absolute;right:20px;bottom:-3px;width:66px;height:25px;background:#000;color:var(--white);font-size:13px;text-align:center;line-height:26px;border-radius:3px 3px 0 0}
.intro{position:absolute;left:280px;top:580px;width:666px;color:var(--text)}
.intro h1{font-size:19px;font-weight:700;color:var(--ink);margin-bottom:8px}
.intro h2{font-size:18px;font-weight:700;color:var(--ink);margin:22px 0 0 2px}
.intro p{font-size:13px;line-height:22px;text-align:justify;padding-left:2px;margin-bottom:22px}
.intro h2+p{margin-bottom:0}
.cards{position:absolute;left:18px;top:943px;width:933px;height:245px}
.card{position:absolute;top:0;width:300px;height:245px;border-radius:8px;background:linear-gradient(180deg,#d6d6d6,#f8f8f8 60%,#e4e4e4);box-shadow:0 8px 10px -6px rgba(0,0,0,.6);padding:20px 22px 0}
.card h3{font-size:27px;font-weight:400;color:var(--card-title);margin-left:2px;line-height:34px;white-space:nowrap;letter-spacing:-.3px}
.card h3.long{font-size:25px;letter-spacing:-.6px}
.card-photo{width:251px;height:62px;margin:4px 0 6px 1px;background:linear-gradient(90deg,#9aa3ad,#e9dccd,#c6b39b)}
.card p{font-family:Arial,sans-serif;font-size:12px;line-height:16px;text-align:justify;color:#111;width:256px}
.card .more{display:block;text-align:right;font-weight:700;font-family:Arial,sans-serif;font-size:12px;color:#111;margin-top:1px}
.footer{position:absolute;left:0;top:1233px;width:970px;height:144px;background:linear-gradient(180deg,var(--red-bright),var(--red-dark));color:var(--white);font-family:Arial,sans-serif;font-size:12px}
.footer-links{position:absolute;left:22px;top:18px}
.footer-links span{margin-right:10px}
.disclaimer{position:absolute;left:22px;top:53px;width:670px;line-height:18px}
.badge{position:absolute;left:844px;top:28px;width:103px;height:83px;background:var(--white);box-shadow:10px 10px 0 rgba(255,255,255,.25)}
</style>
</head>
<body>
<div class="stage">
  <div class="page">
    <header class="header">
      <div class="brand">
        <div class="brand-square"></div>
        <div>
          <div class="brand-small">LAW OFFICE OF</div>
          <div class="brand-name">MARTA K. DOLVENIDZE</div>
        </div>
      </div>
      <div class="phone">
        <svg width="26" height="26" viewBox="0 0 26 26" aria-hidden="true"><rect width="26" height="26" rx="4" fill="#fff"/><path d="M8 5c-2 1-3 3-2 6 2 5 5 8 9 10 2 1 4 0 5-2l-3-3-2 1c-2-1-4-3-5-5l1-2z" fill="#8a0b16"/></svg>
        415-555-0182
      </div>
    </header>
    <nav class="nav">
      <a class="active">Home</a><a>About Us</a><a>Areas of Practice</a><a>Resources</a><a>Blog</a><a>FAQ</a><a>Contact Us</a>
    </nav>
    <div class="hero" role="img" aria-label="Sunny meadow with yellow flowers, butterflies and a house under a blue sky">
      <div class="hero-tag">Always Protecting Client's Interests!</div>
    </div>
    <form class="contact">
      <h2>CONTACT FORM</h2>
      <p>Fields marked with * are required.</p>
      <div class="field">Name *</div>
      <div class="field">Email *</div>
      <div class="field">Phone</div>
      <div class="field">Subject *</div>
      <div class="field msg">Message *</div>
      <div class="submit">SUBMIT</div>
    </form>
    <section class="intro">
      <h1>Welcome to BK Law Central - Complete Bankruptcy Information</h1>
      <p>Gravel_-_main_pageThe Law Offices of Marta K. Dolvenidze is a consumer law office dedicated to consumer protection and zealously defending the rights of our clients.&nbsp; We offer the big firm quality legal representation with a small firm individualized attention to each client.</p>
      <p>Our office offers services in: all types of consumer bankruptcy filings, i.e. Chapter 7, Chapter 13, Chapter 11, negotiating a settlement of your debts, assisting you in the defense of collection litigation and defending you against foreclosure. Please review our site and see what we may be able to offer you. Feel free to call us at (415) 555-0182 or use our free case evaluation form.</p>
      <h2>Speak to a Lawyer</h2>
      <p>Unlike some other law firms, when you call the Law Office of Marta K. Dolvenidze you will speak to an actual attorney. Not a paralegal or assistant. And even after retaining our office you will still speak to an attorney unlike other firms where you cannot get a hold of your attorney after several attempts.</p>
    </section>
    <section class="cards">
      <article class="card" style="left:0">
        <h3>Debt Relief</h3>
        <div class="card-photo" role="img" aria-label="Photo of a couple meeting with an advisor"></div>
        <p>This page is available, however, but because occasionally circumstances occur in which toil and pain can procure him some great. To take a trivial example, which of us ever undertakes laborious physical exercise, except to obtain some advantage from it.</p>
        <span class="more">read more...</span>
      </article>
      <article class="card" style="left:317px">
        <h3 class="long">Foreclosure Prevention</h3>
        <div class="card-photo" role="img" aria-label="Photo of a smiling family in a car"></div>
        <p>This page is available, however, but because occasionally circumstances occur in which toil and pain can procure him some great. To take a trivial example, which of us ever undertakes laborious physical exercise, except to obtain some advantage from it.</p>
        <span class="more">read more...</span>
      </article>
      <article class="card" style="left:633px">
        <h3>Chapter 13</h3>
        <div class="card-photo" role="img" aria-label="Photo of a relaxed couple at home"></div>
        <p>This page is available, however, but because occasionally circumstances occur in which toil and pain can procure him some great. To take a trivial example, which of us ever undertakes laborious physical exercise, except to obtain some advantage from it.</p>
        <span class="more">read more...</span>
      </article>
    </section>
    <footer class="footer">
      <div class="footer-links"><span>Go to top</span> <span>Copyright © 2010 DKLaw. All Rights Reserved. | Web Development by Webfernly</span></div>
      <p class="disclaimer">Disclaimer: The Law Offices of Marta K. Dolvenidze is a Debt Relief law firm as defined by 11 U.S.C. 528. We help people file for Bankruptcy Relief under the Bankruptcy Code. The information contained on this website is not to be construed as legal advice. It is not intended to solicit or form an attorney-client relationship. We do not guarantee any result and prior results do not guarantee a similar outcome. This is an attorney advertisement and this website is for informational purposes only.</p>
      <div class="badge" role="img" aria-label="Professional association membership badge"></div>
    </footer>
  </div>
</div>
</body>
</html>
```